Corporate Design für eine Veranstaltungsagentur
Vielen Dank an Bartholomä, der trotz vieler unserer Revisionswünsche stets freundlich war, professionell und schnell gearbeitet hat und uns am Ende ein wirklich wunderbares Ergebnis geliefert hat! :-) Wir können ihn uneingeschränkt weiterempfehlen!
Zielgruppe
Agentur zur Planung, Organisation und Durchführung von Veranstaltungen aller Art
Ingenieurbetrieb für Veranstaltungstechnik und - produktion
Organisation und Durchführung der 'Wellenklang'-Veranstaltungsreihe: www.wellenklang-turnier.de
Zielgruppe:
Personen jeder Altersgruppe, Privatpersonen, Geschäftskunden
Aufgabenstellung
Die Farbe Grün sollte beibehalten werden.
Logo soll Professionalität und Innovation ausstrahlen, gleichzeitig modern und zeitlos wirken.

```html
<!DOCTYPE html>
<html lang="de">
<head>
<meta charset="utf-8">
<title>Lumora Events – Geschäftsausstattung</title>
<link href="https://fonts.googleapis.com/css2?family=Open+Sans:wght@400;600;700&family=Ubuntu:wght@400;500&display=swap" rel="stylesheet">
<style>
  :root{
    --stage:#e8e8e6;
    --paper:#ffffff;
    --ink:#2f2f2f;
    --ink-soft:#555555;
    --green:#7dbb2f;
    --green-deep:#3f9a3a;
    --card-dark:#373737;
    --rule:#b9b9b9;
  }
  *{margin:0;padding:0;box-sizing:border-box}
  html,body{width:1200px;height:856px;overflow:hidden}
  body{background:var(--stage);position:relative;font-family:"Open Sans",sans-serif;color:var(--ink)}

  .sheet{position:absolute;background:var(--paper);box-shadow:0 4px 14px rgba(0,0,0,.18)}
  .letterhead{left:78px;top:73px;width:503px;height:712px}
  .card{top:273px;width:198px;height:306px}
  .card--light{left:650px}
  .card--dark{left:903px;background:var(--card-dark)}

  /* word mark */
  .brand{position:absolute;text-align:center;font-family:"Ubuntu",sans-serif;font-weight:500;line-height:.86;color:var(--ink)}
  .brand__dot{display:block;margin:0 auto 6px;border-radius:50%;background:var(--green)}
  .brand--letter{left:385px;top:36px;width:84px;font-size:22px}
  .brand--letter .brand__dot{width:26px;height:26px}
  .brand--card{left:0;top:34px;width:198px;font-size:24px}
  .brand--card .brand__dot{width:30px;height:30px}
  .brand--dark{left:0;top:104px;width:198px;font-size:24px;color:#ffffff}
  .brand--dark .brand__dot{width:30px;height:30px}

  /* letter */
  .sender-line{position:absolute;left:52px;top:108px;font-size:5.2px;color:var(--ink-soft);border-bottom:.6px solid var(--ink-soft);padding-bottom:1px;width:150px}
  .recipient{position:absolute;left:52px;top:128px;font-size:7.8px;line-height:10px}
  .recipient .city{margin-top:10px}
  .subject{position:absolute;left:52px;top:245px;font-size:7.4px;font-weight:700}
  .body-copy{position:absolute;left:52px;top:271px;width:278px;font-size:7.1px;line-height:9.2px;color:var(--ink)}
  .body-copy p{margin-bottom:9px}
  .closing{position:absolute;left:52px;top:620px;font-size:7.3px;color:var(--ink-soft)}
  .signature{position:absolute;left:52px;top:643px;width:104px;height:22px;background:linear-gradient(90deg,#e6e6e6,#f2f2f2);border-radius:2px}
  .signer{position:absolute;left:52px;top:673px;font-size:7.3px;color:var(--ink-soft)}
  .company-info{position:absolute;right:36px;top:518px;width:150px;text-align:right;font-size:4.6px;line-height:6.1px;color:var(--ink)}
  .company-info p{margin-bottom:4px}
  .company-info .accent{color:var(--green)}

  /* card details */
  .card-rule{position:absolute;left:31px;top:137px;width:135px;height:1px;background:var(--rule)}
  .contact{position:absolute;left:0;width:198px;text-align:center;font-family:"Ubuntu",sans-serif;font-size:8.4px;line-height:11px;color:var(--ink)}
  .contact__name{top:160px;font-weight:500}
  .contact__role{color:var(--green)}
  .contact__address{top:190px}
  .contact__lines{top:222px}
  .contact__web{top:260px;color:var(--green);font-weight:500}
</style>
</head>
<body>

<section class="sheet letterhead" aria-label="Briefbogen">
  <div class="brand brand--letter"><span class="brand__dot"></span>lumora<br>events</div>

  <p class="sender-line">Vorname Nachname, Musterstr. 123, 12345 Musterstadt</p>

  <address class="recipient" style="font-style:normal">
    Martina Musterfrau<br>Musterstraße 456
    <div class="city">12345 Berlin</div>
  </address>

  <p class="subject">Quidero molore, atatur sae. Nequat,</p>

  <div class="body-copy">
    <p>Ur sit, imus, ipicatem voluptate eum re dolluptios sequosam, eum reritati am volor sapedissi quo blaboribust, sequass itasped igendi cus exerfer feruptas iusanda ndaest, qui omnis nus aut fugitinis quatur ad ullaut mostem quasperiae corem et aciatem illatin ciduntores quidis utemquam autemperae soluptiae lab illacescia solorum et fugiam ratatatus exerro blaciis samusam etur? Uga. Neque nam simi, nest, ommod essedios magnatia nossi aute nonsequam fugiaspis moluptas sed el int etur saepe nonsecatem excea noneceperrum ulligendit faccullores et lantur si ium at.Ota cuptae non ea de opta voles rem rae dolore ilia vellab isi blanis idit veribus auda alit labore desenis imenis que in con rehent, explat ped que volorum, autent, si tetur?</p>
    <p>Ihil ium restior ecepero reptistius es aborepe diatiunt dignis diciae voluptu ribearit, que nat aute et as maximus, qui blab iur aut volest, nonsequae odios doluptatiae velignimin perescia vent.<br>Pa voluptas expero corectur molest eaquid enda vidus verciis quodi te dit aliquid unturem poreper feratur? Quis aut rehenihilit et quam, eris et perorru mquamusa quo et untia volupie nisimoluptae esseribus cora doluptati doluptatur atsciumqui re pa quat aut lam solescia intiis et millabor sit odis et quos re sam, vendicientur abo. Equi totatus rest, nosam quodi omni doloriosam des ea nimpelique volo elendae dellign ihilitis solupta temporp orupta iuntia ipiste natibusapis volesedis reriori taerrup tatiberes nobitiur, sequi omnihillab id maximagnat omnimus dolo quunt, int aut earum lacit peliquunt iduciet, id que autemolum deruptati te non re.</p>
    <p>Ur sit, imus, ipicatem voluptate eum re dolluptios sequosam, eum reritati am volor sapedissi quo blaboribust, sequass itasped igendi cus exerfer feruptas iusanda ndaest, qui omnis nus aut fugitinis quatur ad ullaut mostem quasperiae corem et aciatem illatin ciduntores quidis utemquam autemperae soluptiae lab illacescia solorum et fugiam ratatatus exerro blaciis samusam etur? Uga. Neque nam simi, nest, ommod essedios magnatia nossi aute nonsequam fugiaspis moluptas sed el int etur saepe nonsecatem excea noneceperrum ulligendit faccullores et lantur si ium at.</p>
    <p>Ihil ium restior ecepero reptistius es aborepe diatiunt dignis diciae voluptu ribearit, que nat aute et as maximus, qui blab iur aut volest, nonsequae odios doluptatiae velignimin perescia vent.</p>
  </div>

  <p class="closing">Sincerely</p>
  <div class="signature" role="img" aria-label="Handschriftliche Unterschrift"></div>
  <p class="signer">Max Mustermann</p>

  <div class="company-info">
    <p class="accent">Lumora Events UG<br>(haftungsbeschränkt)</p>
    <p>Kastanienweg 7<br>48210 Talbrunn</p>
    <p>T: (02 31) 874 20 615<br>F: (02 31) 874 20 616<br>hallo@lumora-events.de</p>
    <p>Geschäftsführer:<br>Jonas Wehrfeld</p>
    <p>Sitz der Gesellschaft:<br>Talbrunn</p>
    <p>Eingetragen beim<br>Amtsgericht Talbrunn<br>HR B 41 18</p>
    <p>USt.-Id.-Nr. DE 417 603 285</p>
    <p>Talbrunner Volksbank<br>IBAN DE58310500004417203966<br>BIC TALBDE31XXX</p>
    <p class="accent">www.lumora-events.de</p>
  </div>
</section>

<section class="sheet card card--light" aria-label="Visitenkarte Vorderseite">
  <div class="brand brand--card"><span class="brand__dot"></span>lumora<br>events</div>
  <div class="card-rule"></div>
  <p class="contact contact__name">Vorname Nachname<br><span class="contact__role">Geschäftsführung</span></p>
  <p class="contact contact__address">Musterstr. 123<br>12345 Musterstadt</p>
  <p class="contact contact__lines">T: 010 / 123 456 789<br>F: 010 / 123 456 790<br>info@beispielseite.de</p>
  <p class="contact contact__web">www.beispielseite.de</p>
</section>

<section class="sheet card card--dark" aria-label="Visitenkarte Rückseite">
  <div class="brand brand--dark"><span class="brand__dot"></span>lumora<br>events</div>
</section>

</body>
</html>
```